Need to drive pregnant women to my 3d4d ultrasound studio where i provide 4d ultrasound with hyperalistic imaging and gender reveals

Industry/Entity Type

Healthcare

Font styles to use
Decorative
Script

Requirements
Must have
• My Company name Cielo de Nuestra Espera 4D. EVERYTHING HAS TO BE IN SPANISH
Nice to have
• SIMPLE AND NOT TOO BUSY
Should not have
• website

```html
<!DOCTYPE html>
<html lang="es">
<head>
<meta charset="utf-8">
<title>Cielo de Nuestra Espera 4D</title>
<link rel="stylesheet" href="https://fonts.googleapis.com/css2?family=Allura&family=Cinzel:wght@400&display=swap">
<style>
  :root {
    --stage: #e6e4e8;
    --banner: #000000;
    --ink: #ffffff;
    --rule: rgba(255, 255, 255, 0.55);
    --scan-deep: #5a2a08;
    --scan-mid: #b8621c;
    --scan-light: #e39a4a;
    --ui-bar: #0e3346;
    --ui-frame: #9aa3a8;
    --skin-light: #f0d3c4;
    --skin-mid: #d9ad98;
    --photo-shade: #3a2620;
  }
  * { margin: 0; padding: 0; box-sizing: border-box; }
  html, body {
    width: 1200px;
    height: 1191px;
    overflow: hidden;
    background: var(--stage);
  }
  .stage {
    position: relative;
    width: 1200px;
    height: 1191px;
  }
  .billboard {
    position: absolute;
    left: 0;
    top: 421px;
    width: 1200px;
    height: 349px;
    background: var(--banner);
    overflow: hidden;
  }
  .brand-name {
    position: absolute;
    left: 20px;
    width: 860px;
    top: 70px;
    text-align: center;
    font-family: "Allura", cursive;
    font-weight: 400;
    font-size: 84px;
    line-height: 1;
    color: var(--ink);
    white-space: nowrap;
  }
  .divider {
    position: absolute;
    left: 47px;
    top: 187px;
    width: 790px;
    height: 1px;
    background: linear-gradient(90deg, transparent, var(--rule) 15%, var(--rule) 85%, transparent);
  }
  .tagline {
    position: absolute;
    left: 20px;
    width: 860px;
    top: 213px;
    text-align: center;
    font-family: "Cinzel", serif;
    font-size: 25px;
    line-height: 38px;
    color: var(--ink);
    letter-spacing: 0.3px;
    white-space: nowrap;
  }
  .scan-screen {
    position: absolute;
    left: 914px;
    top: 18px;
    width: 235px;
    height: 162px;
    background: #000;
  }
  .scan-screen .ui-bar {
    height: 14px;
    background: var(--ui-bar);
  }
  .scan-screen .scan-view {
    position: absolute;
    left: 0;
    top: 18px;
    width: 185px;
    height: 140px;
    border: 1px solid var(--ui-frame);
    background: #000;
  }
  .scan-screen .scan-image {
    position: absolute;
    left: 28px;
    top: 2px;
    width: 128px;
    height: 134px;
    background: radial-gradient(ellipse at 45% 45%, var(--scan-light), var(--scan-mid) 45%, var(--scan-deep) 90%);
  }
  .scan-crop {
    position: absolute;
    left: 914px;
    top: 198px;
    width: 103px;
    height: 132px;
    background: radial-gradient(ellipse at 55% 50%, var(--scan-light), var(--scan-mid) 50%, var(--scan-deep));
  }
  .newborn-photo {
    position: absolute;
    left: 1031px;
    top: 198px;
    width: 119px;
    height: 132px;
    background: radial-gradient(ellipse at 55% 50%, var(--skin-light), var(--skin-mid) 55%, var(--photo-shade));
  }
</style>
</head>
<body>
  <main class="stage">
    <section class="billboard">
      <h1 class="brand-name">Cielo de Nuestra Espera 4D</h1>
      <div class="divider"></div>
      <p class="tagline">Ofrecemos Ultrasonido 4D Con<br>Imágenes Hiperrealistas Y Revelación De Género</p>

      <div class="scan-screen">
        <div class="ui-bar"></div>
        <div class="scan-view">
          <div class="scan-image" role="img" aria-label="Ecografía 4D de un bebé en el vientre"></div>
        </div>
      </div>
      <div class="scan-crop" role="img" aria-label="Detalle de ecografía 4D del rostro del bebé"></div>
      <div class="newborn-photo" role="img" aria-label="Fotografía de un recién nacido dormido"></div>
    </section>
  </main>
</body>
</html>
```